Bring me business with this creative business card

Design my new business card. I am looking for something different with an impact. People will take a look at this card & they will 1- see how different & creative I am, 2-understand what I do 3- Call me to meet me!

I make videos with a message, testimonials. I am dynamic, fun, creative & human. My new website is in construction but in the meantime you can check this old one: brightpath.ca & another one Tidebloom.com & tidebloom facebook page.
I make videos. sometimes with a cameraman, sometimes with my phone. As an ex Public Relations agent, the message is the most important thing for me. I want to make my clients shine! When they start with me they often remind me of a lamb, when I finish coaching them they are powerful like LIONS! That's why I need a powerful business card!

Target Market(s)

Entrepreneurs, solo entrepreneurs, small & medium companies & start ups. People i will meet while networking. People that need videos on their website & social Networks to get attention, to be visible. men & women. From 35 to 49 years old.
I am an ex Public relations agent. I used to send clients in traditional medias, now with videos they have more chances to be seen on google the new media. I do videos of the president, his team, his loyal clients saying how great the company is & expert videos like series so people can be seen for example every 1 st of every month with a short 2 minute video. Also with my 20 years in marketing & communications I can coach & give tips to anybody who needs it.
Target: anybody who would like my old website brightpath.ca & I also have another website but it will be off line soon: tidebloom.com could give you ideas.

Industry/Entity Type

Communications

Contact Information for Business Card

I am in Montreal,So the business cards have to be the usual size like we have in Montreal: 9 cm x 5 cm
Details:My text: Mathilde Tessier Communication coach/Chief Lion. "Stories told the way only you can" off: 514-555-0147 cell: 514-555-0183. tidebloom.com
mathilde@tidebloom.com logo facebook, youtube, instagram

Colors
f37122

Requirements
Must have
• Dynamic, happy. Orange. Be creative in the look but NOT the shape of the card. Easy to read. Big enough to read.
Should not have
• No funny shapes: no round, no square, just the usual. I love creative but NOT on shape.

```html
<!DOCTYPE html>
<html lang="en">
<head>
<meta charset="utf-8">
<title>Tidebloom business card</title>
<link rel="stylesheet" href="https://fonts.googleapis.com/css2?family=Cinzel:wght@600&family=Roboto+Condensed:wght@400;700&display=swap">
<style>
  :root {
    --canvas: #e9e6e1;
    --card-white: #fbfbfa;
    --card-dark: #1f2022;
    --orange: #f37122;
    --orange-light: #f6a21f;
    --orange-deep: #e8501c;
    --ink: #3a3a3a;
    --peach: #fbe6d2;
  }
  * { box-sizing: border-box; margin: 0; padding: 0; }
  html, body { width: 1200px; height: 911px; overflow: hidden; background: var(--canvas); }
  .stage { position: relative; width: 1200px; height: 911px; }

  .card { position: absolute; left: 240px; width: 720px; height: 400px; overflow: hidden;
          box-shadow: 0 6px 18px rgba(0,0,0,.18); }
  .card--front { top: 40px; background: var(--card-white); }
  .card--back  { top: 470px; background: var(--card-dark); }

  /* front */
  .front__backdrop { position: absolute; right: 0; top: 0; width: 330px; height: 270px;
                     background: radial-gradient(ellipse at 60% 45%, #fde7c9 0%, var(--peach) 55%, rgba(251,230,210,0) 100%); opacity: .8; }
  .front__dark-block { position: absolute; left: 0; bottom: 0; width: 120px; height: 210px; background: var(--card-dark); }
  .front__mark { position: absolute; left: 22px; top: 138px; width: 118px; height: 118px; border-radius: 50%;
                 background: var(--orange); }
  .front__brand { position: absolute; left: 168px; top: 128px; }
  .brand-name { font-family: "Cinzel", serif; font-weight: 600; color: var(--orange); letter-spacing: 4px; }
  .front__brand .brand-name { font-size: 50px; line-height: 1; }

  .person { position: absolute; left: 170px; top: 200px; font-family: "Roboto Condensed", sans-serif; }
  .person__name { font-size: 24px; font-weight: 700; color: var(--orange-deep); letter-spacing: .5px; }
  .person__role { font-size: 17px; color: var(--orange-light); line-height: 1.2; text-transform: uppercase; }

  .contacts { position: absolute; left: 170px; top: 286px; list-style: none;
              font-family: "Roboto Condensed", sans-serif; font-size: 16px; color: var(--ink); }
  .contacts li { display: flex; align-items: center; gap: 10px; height: 22px; }
  .contacts svg { width: 13px; height: 13px; fill: var(--orange-deep); flex: none; }

  /* back */
  .back__mark { position: absolute; left: 300px; top: 40px; width: 120px; height: 120px; border-radius: 50%;
                background: var(--orange); }
  .back__brand { position: absolute; left: 0; right: 0; top: 182px; text-align: center; }
  .back__brand .brand-name { font-size: 54px; line-height: 1; }
  .back__slogan { margin-top: 22px; font-family: "Roboto Condensed", sans-serif; font-size: 19px; color: var(--orange); }
  .socials { position: absolute; left: 190px; right: 190px; top: 336px; display: flex; align-items: center; gap: 12px; }
  .socials .rule { flex: 1; height: 1.5px; background: var(--orange-deep); opacity: .7; }
  .socials .dot { width: 20px; height: 20px; border-radius: 50%; background: var(--orange-deep); }
</style>
</head>
<body>
<main class="stage">

  <section class="card card--front">
    <div class="front__backdrop" role="img" aria-label="Faint warm-toned background decoration"></div>
    <div class="front__dark-block"></div>
    <div class="front__mark"></div>

    <div class="front__brand">
      <div class="brand-name">TIDEBLOOM</div>
    </div>

    <div class="person">
      <div class="person__name">MATHILDE T.</div>
      <div class="person__role">Communication coach</div>
      <div class="person__role">Chief Lion</div>
    </div>

    <ul class="contacts">
      <li><svg viewBox="0 0 16 16"><path d="M3 1h3l1.5 4-2 1.3a9 9 0 0 0 4.2 4.2L11 8.5 15 10v3a2 2 0 0 1-2 2A12 12 0 0 1 1 3a2 2 0 0 1 2-2z"/></svg>514-555-0147</li>
      <li><svg viewBox="0 0 16 16"><path d="M4 0h8a1 1 0 0 1 1 1v14a1 1 0 0 1-1 1H4a1 1 0 0 1-1-1V1a1 1 0 0 1 1-1zm1 2v10h6V2z"/></svg>514-555-0183</li>
      <li><svg viewBox="0 0 16 16"><path d="M1 3h14v10H1zm1 1v.5l6 4 6-4V4z"/></svg>mathilde@tidebloom.com</li>
      <li><svg viewBox="0 0 16 16"><circle cx="8" cy="8" r="7"/></svg>www.tidebloom.com</li>
    </ul>
  </section>

  <section class="card card--back">
    <div class="back__mark"></div>
    <div class="back__brand">
      <div class="brand-name">TIDEBLOOM</div>
      <div class="back__slogan">Stories told the way only you can</div>
    </div>
    <div class="socials">
      <span class="rule"></span>
      <span class="dot"></span><span class="dot"></span><span class="dot"></span>
      <span class="rule"></span>
    </div>
  </section>

</main>
</body>
</html>
```